LinkedIn Banner Design for B2B Consulting Firm

Take the already developed logo (attached) and incorporate it into a creative banner design for placement on LinkedIn (the social media platform targeting business users). The banner will be used on the firm's company profile page on LinkedIn (not yet created).

```html
<!DOCTYPE html>
<html lang="en">
<head>
<meta charset="utf-8">
<title>Verdant Ridge Advisors – LinkedIn Banner</title>
<link href="https://fonts.googleapis.com/css2?family=PT+Serif:wght@400&display=swap" rel="stylesheet">
<style>
  :root {
    --forest: #466650;
    --sage: #809a7e;
    --mist: #c3d3b8;
    --white: #ffffff;
    --gold: #f4a52c;
  }
  html, body {
    margin: 0;
    padding: 0;
    overflow: hidden;
    background: var(--white);
  }
  .banner {
    position: relative;
    width: 1200px;
    height: 448px;
    overflow: hidden;
    background: var(--white);
    font-family: "PT Serif", Georgia, serif;
  }
  .band-main {
    position: absolute;
    left: 74px; top: 90px;
    width: 1059px; height: 154px;
    background: var(--forest);
  }
  .band-mid {
    position: absolute;
    left: 74px; top: 244px;
    width: 1059px; height: 15px;
    background: var(--sage);
  }
  .band-light {
    position: absolute;
    left: 74px; top: 259px;
    width: 1059px; height: 11px;
    background: var(--mist);
  }
  .brand-card {
    position: absolute;
    left: 115px; top: 172px;
    width: 146px; height: 137px;
    background: var(--white);
    box-shadow: 0 3px 5px rgba(0, 0, 0, 0.25);
    display: flex;
    flex-direction: column;
    align-items: center;
    justify-content: center;
    color: var(--forest);
    text-align: center;
  }
  .brand-name {
    font-size: 17px;
    line-height: 1.1;
    margin: 0;
  }
  .brand-sub {
    font-size: 8px;
    letter-spacing: 6px;
    margin: 8px 0 0 6px;
  }
  .headline-rule {
    position: absolute;
    left: 349px; top: 148px;
    width: 82px; height: 3px;
    border-radius: 2px;
    background: var(--mist);
  }
  .headline {
    position: absolute;
    left: 349px; top: 156px;
    margin: 0;
    font-size: 22.5px;
    font-weight: 400;
    color: var(--white);
    letter-spacing: 0.1px;
    white-space: nowrap;
  }
  .subline {
    position: absolute;
    left: 349px; top: 185px;
    margin: 0;
    font-size: 17px;
    color: var(--mist);
    white-space: nowrap;
  }
  .finance-art {
    position: absolute;
    left: 882px; top: 131px;
    width: 205px; height: 114px;
  }
</style>
</head>
<body>
  <div class="banner">
    <div class="band-main"></div>
    <div class="band-mid"></div>
    <div class="band-light"></div>

    <div class="headline-rule"></div>
    <h1 class="headline">FRACTIONAL MARKETING SERVICES</h1>
    <p class="subline">For Private Equity Firms, Family Offices &amp; Investment Banks</p>

    <svg class="finance-art" viewBox="0 0 205 114" role="img" aria-label="Illustration of a bank building, briefcase, growth chart and gold coins">
      <defs>
        <linearGradient id="art-fill" x1="0" y1="0" x2="1" y2="1">
          <stop offset="0" stop-color="#809a7e"/>
          <stop offset="0.7" stop-color="#c3d3b8"/>
          <stop offset="1" stop-color="#f4a52c"/>
        </linearGradient>
      </defs>
      <rect x="0" y="0" width="205" height="114" rx="6" fill="url(#art-fill)"/>
    </svg>

    <div class="brand-card">
      <p class="brand-name">Verdant Ridge</p>
      <p class="brand-sub">ADVISORS</p>
    </div>
  </div>
</body>
</html>
```